KTR Design Business Card

I need to develop a business card for my real estate design and investment company. Something clean, classic and professional with a modern vibe.

Industry/Entity Type

Real Estate

Font styles to use
Serif
Sans Serif

```html
<!DOCTYPE html>
<html lang="en">
<head>
<meta charset="utf-8">
<title>KTR Design Business Card</title>
<link href="https://fonts.googleapis.com/css2?family=Questrial&display=swap" rel="stylesheet">
<style>
  :root {
    --backdrop: #e7e3de;
    --card: #393939;
    --ink: #ffffff;
    --ink-soft: #f2f2f2;
  }
  * { margin: 0; padding: 0; box-sizing: border-box; }
  html, body {
    width: 1200px;
    height: 1000px;
    overflow: hidden;
    background: var(--backdrop);
    font-family: "Questrial", "Century Gothic", sans-serif;
    color: var(--ink);
  }
  .canvas {
    position: relative;
    width: 1200px;
    height: 1000px;
  }
  .card {
    position: absolute;
    left: 265px;
    width: 666px;
    height: 397px;
    background: var(--card);
  }
  .card--front { top: 73px; }
  .card--back { top: 532px; }

  .brand-name {
    position: absolute;
    font-weight: 400;
    color: var(--ink);
    letter-spacing: 0.5px;
    white-space: nowrap;
  }
  .card--front .brand-name {
    left: 50px;
    top: 168px;
    font-size: 44px;
    line-height: 1;
  }
  .card--back .brand-name {
    left: 0;
    right: 0;
    top: 158px;
    text-align: center;
    font-size: 66px;
    line-height: 1;
  }

  .person {
    position: absolute;
    left: 375px;
    top: 124px;
  }
  .person__name {
    font-size: 20px;
    line-height: 1;
    color: var(--ink);
  }
  .person__role {
    margin-top: 8px;
    font-size: 14px;
    line-height: 1;
    color: var(--ink-soft);
  }

  .contact-list {
    position: absolute;
    left: 375px;
    top: 197px;
    list-style: none;
  }
  .contact-list__item {
    display: flex;
    align-items: center;
    height: 19px;
    font-size: 14.5px;
    color: var(--ink-soft);
  }
  .contact-list__icon {
    width: 10px;
    height: 10px;
    margin-right: 7px;
    flex: none;
  }
</style>
</head>
<body>
<main class="canvas">
  <section class="card card--front" aria-label="Business card front">
    <p class="brand-name">KTR Design</p>

    <div class="person">
      <p class="person__name">Jordan Ellis</p>
      <p class="person__role">Founder</p>
    </div>

    <ul class="contact-list">
      <li class="contact-list__item">
        <svg class="contact-list__icon" viewBox="0 0 10 10" aria-hidden="true">
          <rect x="2.5" y="0.5" width="5" height="9" rx="0.8" fill="none" stroke="#fff" stroke-width="1"/>
        </svg>
        + 1 404 310 2281
      </li>
      <li class="contact-list__item">
        <svg class="contact-list__icon" viewBox="0 0 10 10" aria-hidden="true">
          <path d="M0.5 3.5 Q5 0 9.5 3.5 L8 5 L6.5 4 L3.5 4 L2 5 Z" fill="#fff"/>
          <rect x="2" y="5" width="6" height="4" rx="0.6" fill="#fff"/>
        </svg>
        + 1 404 310 7754
      </li>
      <li class="contact-list__item">
        <svg class="contact-list__icon" viewBox="0 0 10 10" aria-hidden="true">
          <rect x="0.5" y="2" width="9" height="6.5" fill="#fff"/>
          <path d="M0.5 2 L5 5.8 L9.5 2" fill="none" stroke="#393939" stroke-width="0.9"/>
        </svg>
        info@ktrdesignstudio.com
      </li>
      <li class="contact-list__item">
        <svg class="contact-list__icon" viewBox="0 0 10 10" aria-hidden="true">
          <circle cx="5" cy="5" r="4.4" fill="none" stroke="#fff" stroke-width="1"/>
          <ellipse cx="5" cy="5" rx="1.9" ry="4.4" fill="none" stroke="#fff" stroke-width="0.8"/>
          <line x1="0.6" y1="5" x2="9.4" y2="5" stroke="#fff" stroke-width="0.8"/>
        </svg>
        www.ktrdesignstudio.com
      </li>
    </ul>
  </section>

  <section class="card card--back" aria-label="Business card back">
    <p class="brand-name">KTR Design</p>
  </section>
</main>
</body>
</html>
```